New profile page for existing party website

For the party website 'Partyvenz' we need a new design for the user profile page.

The page should show
* a profile picture
* basic information like name, age and city
* music styles he/she likes
* links to their Chatterbook profile and website
* a bio (HTML content)
* events they plan to go to
* past events
* pictures

Challenge is that some users may have little information (just their name) while others have a huge description, lots of foto's, events, etc.

Please visit http://www.partyvenz.example and http://www.partyvenz.example/users/bertil

Target Market(s)

Men and women between 18 and 35

Industry/Entity Type

Night Club

Number of Pages Required

2 page

Font styles to use
Other font styles liked:
• Roboto

Requirements
Must have
• Please design how the page looks with a fully filled out profile and with an empty profile.
• It should fit well with the existing website.
• Include designs for both for small screens (mobile) and large screens (tablet, desktop).
Nice to have
• UX design on how to collapse or paginate sections.
• Interactive effects would be a bonus.
Should not have
• The page should not have subnavigation like menus or tabs.

```html
<!DOCTYPE html>
<html lang="nl">
<head>
<meta charset="utf-8">
<title>Partyvenz – Profiel</title>
<link href="https://fonts.googleapis.com/css2?family=Roboto+Condensed:wght@400;700&family=Raleway:wght@400;600;700&display=swap" rel="stylesheet">
<style>
  :root {
    --page-bg: #262626;
    --header-bg: #000000;
    --gold: #d89a00;
    --gold-dark: #b98100;
    --gold-frame: #a87400;
    --orange: #d46a17;
    --orange-dark: #b4560f;
    --white: #ffffff;
    --cream: #fff3d6;
  }
  * { box-sizing: border-box; margin: 0; padding: 0; }
  html, body { width: 800px; height: 1200px; overflow: hidden; background: var(--page-bg); }
  body { position: relative; font-family: "Raleway", sans-serif; color: var(--white); }

  .site-header {
    position: absolute; left: 0; top: 0; width: 800px; height: 56px;
    background: var(--header-bg);
  }
  .brand {
    position: absolute; left: 10px; top: 12px;
    font-family: "Roboto Condensed", sans-serif; font-size: 30px; font-weight: 400;
    color: var(--white); letter-spacing: 0.5px;
  }
  .menu-toggle {
    position: absolute; left: 738px; top: 6px; width: 46px; height: 35px;
    border: 1px solid #555; border-radius: 4px;
  }
  .menu-toggle svg { position: absolute; left: 11px; top: 10px; }

  .panel { position: absolute; left: 18px; width: 760px; }
  .panel-profile { top: 72px; height: 562px; background: var(--gold); }
  .panel-resume { top: 659px; height: 541px; background: var(--orange); overflow: hidden; }

  .panel-tab { position: absolute; left: 0; top: 0; height: 43px; display: flex; gap: 2px; }
  .tab-icon, .tab-label { height: 43px; display: flex; align-items: center; justify-content: center; }
  .tab-icon { width: 46px; }
  .tab-label {
    font-family: "Roboto Condensed", sans-serif; font-size: 19px; color: var(--white);
  }
  .panel-profile .tab-icon, .panel-profile .tab-label { background: var(--gold-dark); }
  .panel-profile .tab-label { width: 135px; }
  .panel-resume .tab-icon, .panel-resume .tab-label { background: var(--orange-dark); }
  .panel-resume .tab-label { width: 122px; }

  .profile-photo {
    position: absolute; left: 275px; top: 72px; width: 210px; height: 244px;
    border: 5px solid var(--gold-frame);
    background: linear-gradient(160deg, #5a3a22 0%, #8a5f3e 45%, #3b2516 100%);
  }
  .profile-name {
    position: absolute; left: 0; width: 760px; top: 329px; text-align: center;
    font-family: "Roboto Condensed", sans-serif; font-size: 25px; font-weight: 400;
  }
  .profile-facts {
    position: absolute; left: 0; width: 760px; top: 368px; text-align: center;
    list-style: none; font-size: 15px; line-height: 23px; color: var(--cream);
  }
  .profile-facts b { font-weight: 700; color: var(--white); }
  .profile-links {
    position: absolute; left: 0; width: 760px; top: 443px;
    display: flex; justify-content: center; gap: 8px;
  }
  .link-square { width: 16px; height: 16px; border-radius: 3px; background: var(--white); }
  .btn-manage {
    position: absolute; left: 318px; top: 490px; width: 125px; height: 40px;
    border: 2px solid var(--gold-frame); border-radius: 4px; background: var(--gold-dark);
    font-family: "Raleway", sans-serif; font-size: 14px; font-weight: 600; color: var(--white);
    display: flex; align-items: center; justify-content: center;
  }

  .resume-body { position: absolute; left: 30px; top: 66px; width: 700px; }
  .resume-title { font-family: "Roboto Condensed", sans-serif; font-size: 23px; font-weight: 400; margin-bottom: 12px; }
  .resume-line { font-size: 15px; margin-bottom: 12px; }
  .resume-line .key { font-family: "Roboto Condensed", sans-serif; font-size: 18px; }
  .resume-heading { font-family: "Roboto Condensed", sans-serif; font-size: 18px; margin-bottom: 14px; }
  .resume-intro { font-size: 15px; line-height: 20.5px; margin-bottom: 18px; }
  .resume-notice { font-family: "Roboto Condensed", sans-serif; font-size: 18px; line-height: 20.5px; }
</style>
</head>
<body>
  <header class="site-header">
    <div class="brand">Partyvenz</div>
    <div class="menu-toggle">
      <svg width="24" height="16" viewBox="0 0 24 16"><rect y="0" width="24" height="2" fill="#fff"/><rect y="7" width="24" height="2" fill="#fff"/><rect y="14" width="24" height="2" fill="#fff"/></svg>
    </div>
  </header>

  <section class="panel panel-profile">
    <div class="panel-tab">
      <div class="tab-icon">
        <svg width="18" height="20" viewBox="0 0 18 20"><circle cx="9" cy="5.5" r="5" fill="#fff"/><path d="M0 20 Q0 11 9 11 Q18 11 18 20 Z" fill="#fff"/></svg>
      </div>
      <div class="tab-label">My Profile</div>
    </div>
    <div class="profile-photo" role="img" aria-label="Profielfoto van Bertil Jansen"></div>
    <h1 class="profile-name">Bertil Jansen</h1>
    <ul class="profile-facts">
      <li><b>Age</b> - 34</li>
      <li><b>City</b> - Amsterdam,</li>
      <li><b>Music</b> - Latin / Salsa</li>
    </ul>
    <div class="profile-links">
      <span class="link-square" aria-label="Chatterbook"></span>
      <span class="link-square" aria-label="Video kanaal"></span>
      <span class="link-square" aria-label="Website"></span>
      <svg width="19" height="16" viewBox="0 0 19 16" aria-label="E-mail"><rect x="0" y="1" width="19" height="14" rx="1.5" fill="#fff"/><path d="M0.5 2 L9.5 9 L18.5 2" fill="none" stroke="#d89a00" stroke-width="1.6"/></svg>
    </div>
    <div class="btn-manage">Manage</div>
  </section>

  <section class="panel panel-resume">
    <div class="panel-tab">
      <div class="tab-icon">
        <svg width="24" height="20" viewBox="0 0 24 20"><rect x="1.5" y="3.5" width="16" height="15" rx="2" fill="none" stroke="#fff" stroke-width="2"/><path d="M8 13 L9 9.5 L19 0.5 L22 3.5 L12 12.5 Z" fill="#fff"/></svg>
      </div>
      <div class="tab-label">Resume</div>
    </div>
    <div class="resume-body">
      <h2 class="resume-title">LensLoop Photography</h2>
      <p class="resume-line"><span class="key">Function :</span> Head promotions, photograper, communication, marketing, and sales.</p>
      <p class="resume-line"><span class="key">Active since :</span> jan 2006</p>
      <p class="resume-line"><span class="key">Shoots :</span> 500 and counting</p>
      <h3 class="resume-heading">Wil jij fotograferen voor Partyvenz?</h3>
      <p class="resume-intro">Als je uitgaan leuk vindt, makkelijk bent in de omgang en uiteraard houdt van fotograferen, biedt Partyvenz je de kans een kijkje te nemen in de wereld van de partyfotografie. Door de inzet van de fotografen is Partyvenz uitgegroeid tot een van de meest toonaangevende party-sites van Nederland. De betrouwbaarheid, de hoge kwaliteit van de foto's en het coveren van de belangrijkste evenementen maakt van Partyvenz een van de best bezochte websites in ons vakgebied.</p>
      <p class="resume-notice">Belangrijk informatie<br>Fotograferen voor Partyvenz is op vrijwillige basis. Je kan kiezen waar en wanneer je uitgaat en foto's maakt, maar een vaste inbreng word wel van je verwacht. Hoe meer je voor Partyvenz doet, hoe meer ervaring je opdoet met de camera en hoe beter je word. Hierdoor kan je weer naar interessantere feesten en festivals. Wat je wel krijgt is gratis entree voor een evenement en soms ook andere voordelen zoals gratis drankjes... Je gaat meestal met ze tweetjes op pad en ontmoet veel nieuwe mensen zoals DJ's en organisatoren. Hoe meer je voor Partyvenz.example werkt hoe meer ervaring je er ook uit zal halen. De beste fotografen doen de leukste en de</p>
    </div>
  </section>
</body>
</html>
```